Business card design for Automotive workshop

We need a business card for a new automotive repair and tyre shop called Keelstone Prime Automotive located in New Zealand. We are a clean, modern and fresh workshop and company.

Front needs to feature logo,
my name:
Marlo Fenwicke (director)

Address:
48 Tarn Lane
Harrow Bay 3627

Phone: 07 594 2713
Mobile: 027 451 9362
Email: office@keelstoneautomotive.example.nz
Website: keelstoneautomotive.example.nz

Back needs to feature an area to write down appointment details, date and time.

Also feature a list of jobs and work we do such as,
Vehicle Servicing
All Mechanical Repairs
Warrant of Fitness
Tyres & Wheel Alignments
Automotive Diagnostics
Automotive Parts & Supplies

```html
<!DOCTYPE html>
<html lang="en">
<head>
<meta charset="utf-8">
<title>Keelstone Prime Automotive – Business Card</title>
<link rel="stylesheet" href="https://fonts.googleapis.com/css2?family=Arimo:wght@400;700&family=Open+Sans:wght@400;600;700&display=swap">
<style>
  :root {
    --red: #e41e26;
    --ink: #2b2b2b;
    --muted: #555;
    --rule: #c9c9c9;
    --paper: #ffffff;
    --stage: #e6e6e6;
  }
  * { box-sizing: border-box; margin: 0; padding: 0; }
  html, body { width: 1200px; height: 1015px; overflow: hidden; }
  body {
    background: var(--stage);
    position: relative;
    font-family: "Arimo", Arial, sans-serif;
    color: var(--ink);
  }
  .card {
    position: absolute;
    left: 220px;
    width: 760px;
    height: 434px;
    background: var(--paper);
    box-shadow: 0 6px 18px rgba(0,0,0,.18);
    overflow: hidden;
  }
  .card--back { top: 49px; }
  .card--front { top: 532px; }

  .card__band {
    position: absolute;
    right: 0;
    bottom: 0;
    height: 34px;
    background: var(--red);
    clip-path: polygon(8px 0, 100% 0, 100% 100%, 0 100%);
  }
  .card--back .card__band { left: 470px; }
  .card--front .card__band { left: 500px; }

  /* Back */
  .appointment__title {
    position: absolute;
    left: 200px; top: 62px;
    color: var(--red);
    font-weight: 700;
    font-size: 27px;
    letter-spacing: .5px;
  }
  .appointment__field {
    position: absolute;
    left: 70px;
    width: 470px;
    display: flex;
    align-items: flex-end;
    font-size: 21px;
    color: var(--ink);
  }
  .appointment__field--date { top: 126px; }
  .appointment__field--time { top: 176px; left: 100px; width: 440px; }
  .appointment__line {
    flex: 1;
    border-bottom: 1px solid var(--rule);
    margin-left: 16px;
    margin-bottom: 5px;
  }
  .services {
    position: absolute;
    list-style: none;
    font-size: 19px;
    line-height: 27px;
  }
  .services--left { left: 70px; top: 268px; }
  .services--right { left: 410px; top: 236px; }
  .services li { position: relative; padding-left: 20px; }
  .services li::before {
    content: "";
    position: absolute;
    left: 0; top: 12px;
    width: 9px; height: 9px;
    border-radius: 50%;
    background: var(--red);
  }

  /* Front */
  .brand {
    position: absolute;
    left: 56px; top: 190px;
    display: flex;
    align-items: center;
    gap: 10px;
    font-family: "Open Sans", Arial, sans-serif;
    font-weight: 700;
    font-size: 21px;
    color: var(--ink);
    letter-spacing: .5px;
    line-height: 1.1;
  }
  .brand__mark { width: 16px; height: 16px; background: var(--red); flex: none; }
  .divider {
    position: absolute;
    left: 372px; top: 100px;
    width: 1px; height: 240px;
    background: var(--rule);
  }
  .contact {
    position: absolute;
    left: 396px; top: 92px;
    font-family: "Open Sans", Arial, sans-serif;
    font-size: 16px;
    color: var(--ink);
    line-height: 23px;
  }
  .contact__name { color: var(--red); font-weight: 700; font-size: 24px; line-height: 30px; letter-spacing: .3px; }
  .contact__role { font-size: 16px; margin-bottom: 10px; }
  .contact__address { font-style: normal; margin-bottom: 10px; }
  .contact__list { list-style: none; }
  .contact__list li { display: flex; align-items: center; gap: 8px; }
  .contact__list svg { width: 14px; height: 14px; flex: none; }
</style>
</head>
<body>

<section class="card card--back" aria-label="Card back">
  <h2 class="appointment__title">NEXT APPOINTMENT</h2>
  <div class="appointment__field appointment__field--date"><span>DATE</span><span class="appointment__line"></span></div>
  <div class="appointment__field appointment__field--time"><span>TIME</span><span class="appointment__line"></span></div>
  <ul class="services services--left">
    <li>Vehicle Servicing</li>
    <li>All Mechanical Repairs</li>
    <li>Warrant of Fitness</li>
  </ul>
  <ul class="services services--right">
    <li>Tyres &amp; Wheel Alignments</li>
    <li>Automotive Diagnostics</li>
    <li>Automotive Parts &amp; Supplies</li>
  </ul>
  <div class="card__band"></div>
</section>

<section class="card card--front" aria-label="Card front">
  <div class="brand"><span class="brand__mark"></span><span>KEELSTONE PRIME<br>AUTOMOTIVE</span></div>
  <div class="divider"></div>
  <div class="contact">
    <div class="contact__name">MARLO FENWICKE</div>
    <div class="contact__role">Director</div>
    <address class="contact__address">48 Tarn Lane<br>Harrow Bay 3627</address>
    <ul class="contact__list">
      <li>
        <svg viewBox="0 0 14 14" aria-hidden="true"><path fill="#e41e26" d="M1 4c0-2 2-3 6-3s6 1 6 3v1h-3V4H4v1H1z M3 6h8l2 6H1z"/></svg>
        07 594 2713
      </li>
      <li>
        <svg viewBox="0 0 14 14" aria-hidden="true"><rect x="3" y="1" width="8" height="12" rx="1.5" fill="none" stroke="#e41e26" stroke-width="1.6"/></svg>
        027 451 9362
      </li>
      <li>
        <svg viewBox="0 0 14 14" aria-hidden="true"><rect x="1" y="3" width="12" height="8" fill="#e41e26"/><path d="M1 3l6 5 6-5" fill="none" stroke="#fff" stroke-width="1.2"/></svg>
        office@keelstoneautomotive.example.nz
      </li>
      <li>
        <svg viewBox="0 0 14 14" aria-hidden="true"><circle cx="7" cy="7" r="6" fill="#e41e26"/><path d="M1 7h12M7 1c-3 3-3 9 0 12M7 1c3 3 3 9 0 12" fill="none" stroke="#fff" stroke-width=".9"/></svg>
        keelstoneautomotive.example.nz
      </li>
    </ul>
  </div>
  <div class="card__band"></div>
</section>

</body>
</html>
```